Luxury Real Estate Website, Midwest, United States

We need web design services for a luxury website. We need IDX Integration with our MLS. We want this to be a very simple website with amazing graphics. We want it to link up with our MailChimp account in order to generate leads through a "More Information" Pop up on the main page. We want the main page to be covered with one large graphic that is a rolling slideshow of active listings of $400,000 and up from the IDX Integration. We need this website to give a very exclusive and sleek look. Lots of black is good... I will upload our logos in Black and Silver. We will also need an "About" page that we are going to call "Qeno Info". We want our graphics to be extremely impressive. Keep in mind, we are a company in the Midwest of the United States, and our real estate has a different look than homes in California or Florida. We need graphics that are realistic for the Midwest, yet still high-end.
Target Market(s)
Luxury Homeowners in the Midwest United States. The graphics needs to be pristine.
Industry/Entity Type
Real Estate
Coding
Coded - Design and coding required
Number of Pages Required
3 page
Requirements
Must have
- Large graphics with IDX Integration. The photos of real estate need to represent real estate that is common in the Midwest, United States. We also need MailChimp integration. We need a pop up that is titled "My Free Market Analysis" that makes them fill out a contact form asking for Full Name, Email Address, Phone Number and Address. This needs to be a pop up on the front page and will integrate with our MailChimp account. We also need a page called "About Qe No Home". And another page where clients can download informational PDFs. The main component needs to be a front page search engine connected with the IDX to access active listings from our MLS. I attached our logos and a sample front page of a website. I would love for ours to look similar.
Nice to have
- Lake House photos on midwest lakes are a plus.
Should not have
- Should not have clutter. This website needs to be clean, luxurious and exclusive.

```html
<!DOCTYPE html>
<html lang="en">
<head>
<meta charset="utf-8">
<title>Hearth Lane Realty Group</title>
<link href="https://fonts.googleapis.com/css2?family=Jost:wght@400;500;600;700&family=Lato:wght@400;700&display=swap" rel="stylesheet">
<style>
:root{
  --ink:#1e1e1e;
  --text:#333;
  --accent:#8fa6c9;
  --accent-soft:#cfdbea;
  --band:#c9d6e6;
  --grey-row:#ececec;
  --gallery-bg:#efefef;
  --footer:#3d3d3d;
  --white:#fff;
}
*{margin:0;padding:0;box-sizing:border-box}
html,body{width:1200px;height:3871px;overflow:hidden}
body{position:relative;background:var(--white);font-family:"Lato",sans-serif;color:var(--text)}
.abs{position:absolute}
.heading{font-family:"Jost",sans-serif}

/* Hero */
.hero-top{left:0;top:0;width:1200px;height:700px;background:#e6ebf1}
.hero-band{left:0;top:0;width:1200px;height:697px;background:var(--band);clip-path:polygon(0 560px,1200px 560px,1200px 697px,0 697px)}
.hero-photo{left:0;top:0;width:1200px;height:697px;
  background:linear-gradient(180deg,#6a7780 0%,#59676b 22%,#44553f 46%,#2f4129 64%,#3a4a52 78%,#1f2b26 100%);
  clip-path:polygon(0 105px,460px 0,1200px 0,1200px 580px,0 697px)}
.brand{font-family:"Jost",sans-serif;font-weight:500;color:var(--white);letter-spacing:2px}
.brand-top{left:98px;top:28px;font-size:30px;line-height:44px}
.nav{right:98px;top:82px;display:flex;gap:38px;font-family:"Jost",sans-serif;font-weight:500;font-size:14px;color:var(--white);letter-spacing:.3px}
.hero-title{left:0;width:1200px;top:232px;text-align:center;font-family:"Jost",sans-serif;font-weight:600;font-size:56px;letter-spacing:2px;color:var(--white)}
.hero-text{left:200px;width:800px;top:330px;text-align:center;font-size:15px;line-height:26px;color:var(--white)}
.btn{left:544px;top:434px;width:120px;height:48px;border:1.5px solid var(--white);color:var(--white);font-family:"Jost",sans-serif;font-size:15px;display:flex;align-items:center;justify-content:center}
.hero-arrows{left:1050px;top:628px}

/* Welcome */
.welcome-photo{left:98px;top:782px;width:346px;height:456px;background:linear-gradient(180deg,#5f7a99 0%,#93a7ba 28%,#7a5a3c 52%,#4d4438 68%,#2f3b44 100%)}
.h-dark{font-family:"Jost",sans-serif;font-weight:600;color:var(--ink)}
.h-accent{font-family:"Jost",sans-serif;font-weight:500;color:var(--accent)}
.welcome-h1{left:480px;top:790px;font-size:38px}
.welcome-h2{left:480px;top:838px;font-size:38px}
.welcome-p{left:480px;width:622px;font-size:13.5px;line-height:22px;text-align:justify;color:#444}
.stat{top:1150px}
.stat .num{font-family:"Jost",sans-serif;font-weight:500;font-size:36px;color:var(--accent);line-height:44px}
.stat .lbl{font-family:"Jost",sans-serif;font-weight:600;font-size:14px;color:#333}

/* Benefits */
.benefits{left:0;top:1321px;width:1200px;height:730px;background:linear-gradient(180deg,#8a9bb6 0%,#7f92ae 45%,#6f839f 75%,#889ab3 100%)}
.sec-title{left:0;width:1200px;text-align:center;font-family:"Jost",sans-serif;font-weight:500;font-size:34px}
.rule{height:2px;width:90px;left:555px}
.ring{border:2px solid var(--white);border-radius:50%;display:flex;align-items:center;justify-content:center}
.benefit-name{width:340px;text-align:center;font-family:"Jost",sans-serif;font-weight:600;font-size:18px;color:var(--white);letter-spacing:.5px}
.benefit-text{width:300px;text-align:center;font-size:13px;line-height:20px;color:var(--white)}

/* Highlights */
.hl-p{left:98px;width:622px;font-size:13.5px;line-height:22px;color:#444}
.acc{left:98px;width:622px;height:44px;display:flex;align-items:center;gap:14px;padding-left:12px;font-family:"Jost",sans-serif;font-size:15px;color:var(--ink)}
.acc-open{background:var(--accent-soft)}
.acc-row{background:var(--grey-row)}
.hl-photo{left:756px;top:2131px;width:346px;height:457px;background:linear-gradient(180deg,#9bb3cf 0%,#b8c8d9 25%,#b5763f 45%,#8d5a33 60%,#48505a 78%,#2e3946 100%)}

/* Gallery */
.gallery{left:0;top:2683px;width:1200px;height:715px;background:var(--gallery-bg)}
.tile{border:0}
.caption{left:100px;top:3251px;width:444px;height:62px;background:rgba(60,70,90,.7);color:var(--white);font-family:"Jost",sans-serif;font-weight:500;font-size:20px;display:flex;align-items:center;padding-left:22px;letter-spacing:.5px}

/* Footer */
.footer{left:0;top:3398px;width:1200px;height:473px;background:var(--footer)}
.foot-text{left:98px;width:440px;top:3578px;font-size:13px;line-height:21px;color:var(--white)}
.social{width:34px;height:34px;border:1.5px solid var(--white);border-radius:50%}
.foot-h{font-family:"Jost",sans-serif;font-weight:500;font-size:22px;color:var(--white)}
.foot-rule{height:2px;width:56px;background:var(--white)}
.links{left:624px;top:3548px;list-style:none}
.links li{display:flex;align-items:center;gap:12px;height:31px;font-size:14px;color:var(--white)}
.contact-icon{width:34px;height:34px;border:1.5px solid var(--white);border-radius:50%;display:flex;align-items:center;justify-content:center}
.contact-lbl{font-family:"Jost",sans-serif;font-weight:600;font-size:14px;color:var(--white)}
.contact-val{font-size:12.5px;color:var(--white);line-height:18px}
.foot-line{left:98px;top:3793px;width:1004px;height:1px;background:#6a6a6a}
.copy{left:0;width:1200px;top:3822px;text-align:center;font-size:13px;color:var(--white)}
</style>
</head>
<body>

<!-- Hero -->
<div class="abs hero-top"></div>
<div class="abs hero-band"></div>
<div class="abs hero-photo" role="img" aria-label="Lake house among pines at dusk reflected in a calm Midwest lake"></div>
<div class="abs brand brand-top">HEARTH LANE</div>
<nav class="abs nav"><span>HOME</span><span>QENO INFO</span><span>ABOUT QE NO HOME</span><span>DOWNLOADS</span><span>CONTACT US</span></nav>
<h1 class="abs hero-title">HEARTH LANE REALTY GROUP</h1>
<p class="abs hero-text">Duis aute irure dolor in reprehenderit in voluptate velit esse cillum dolore eu fugiat nulla pariatur sunt in culpa qui officia deserunt mollit anim id est laborum.</p>
<div class="abs btn">Read More</div>
<svg class="abs hero-arrows" width="46" height="34" viewBox="0 0 46 34" fill="none" stroke="#fff" stroke-width="3"><path d="M14 5 L4 17 L14 29"/><path d="M32 5 L42 17 L32 29"/></svg>

<!-- Welcome -->
<div class="abs welcome-photo" role="img" aria-label="Log cabin with deck on a rocky lakeshore"></div>
<h2 class="abs welcome-h1 h-dark">Welcome To</h2>
<h2 class="abs welcome-h2 h-accent">Hearth Lane Realty Group</h2>
<p class="abs welcome-p" style="top:910px">Nemo enim ipsam voluptatem quia voluptas sit aspernatur aut odit aut fugit, sed quia consequuntur magni dolores eos qui ratione voluptatem sequi nesciunt. Neque porro quisquam est, qui dolorem ipsum quia dolor sit amet, consectetur, adipisci velit, sed quia non numquam eius modi tempora incidunt ut labore et dolore magnam aliquam quaerat voluptatem. Ut enim ad minima veniam, quis nostrum exercitationem ullam corporis suscipit laboriosam.</p>
<p class="abs welcome-p" style="top:1048px">Neque porro quisquam est, qui dolorem ipsum quia dolor sit amet, consectetur, adipisci velit, sed quia non numquam eius modi tempora incidunt ut labore et dolore magnam aliquam quaerat voluptatem. Ut enim ad minima veniam, quis nostrum exercitationem.</p>
<div class="abs stat" style="left:478px"><div class="num">24</div><div class="lbl">Years Experience</div></div>
<div class="abs stat" style="left:672px"><div class="num">550</div><div class="lbl">Projects Completed</div></div>
<div class="abs stat" style="left:896px"><div class="num">2500</div><div class="lbl">Workers Employed</div></div>

<!-- Benefits -->
<div class="abs benefits" role="img" aria-label="Large stone family home with turrets, tinted blue"></div>
<h2 class="abs sec-title" style="top:1380px;color:var(--white)">Our Benefits</h2>
<div class="abs rule" style="top:1446px;background:var(--white)"></div>

<div class="abs ring" style="left:183px;top:1496px;width:114px;height:114px">
  <svg width="48" height="48" viewBox="0 0 48 48" fill="none" stroke="#fff" stroke-width="2.5"><path d="M6 24 L24 8 L42 24"/><path d="M12 20 V40 H36 V20"/><circle cx="24" cy="28" r="5"/></svg>
</div>
<div class="abs ring" style="left:905px;top:1496px;width:114px;height:114px">
  <svg width="48" height="48" viewBox="0 0 48 48" fill="none" stroke="#fff" stroke-width="2.5"><rect x="6" y="8" width="36" height="24" rx="2"/><path d="M16 40 H32 M24 32 V40"/><path d="M17 24 L24 16 L31 24"/></svg>
</div>
<div class="abs ring" style="left:475px;top:1558px;width:248px;height:248px;background:var(--white);border:none">
  <svg width="120" height="120" viewBox="0 0 120 120" fill="#8496b2"><rect x="30" y="20" width="60" height="84"/><rect x="18" y="52" width="14" height="52"/><rect x="88" y="52" width="14" height="52"/><g fill="#fff"><rect x="40" y="30" width="10" height="9"/><rect x="55" y="30" width="10" height="9"/><rect x="70" y="30" width="10" height="9"/><rect x="40" y="46" width="10" height="9"/><rect x="55" y="46" width="10" height="9"/><rect x="70" y="46" width="10" height="9"/><rect x="40" y="62" width="10" height="9"/><rect x="55" y="62" width="10" height="9"/><rect x="70" y="62" width="10" height="9"/><rect x="50" y="80" width="20" height="24"/></g></svg>
</div>
<div class="abs ring" style="left:183px;top:1754px;width:114px;height:114px">
  <svg width="48" height="48" viewBox="0 0 48 48" fill="none" stroke="#fff" stroke-width="2.5"><path d="M8 22 L22 10 L36 22"/><path d="M12 19 V38 H24"/><circle cx="30" cy="30" r="7"/><path d="M35 35 L42 42"/></svg>
</div>
<div class="abs ring" style="left:905px;top:1754px;width:114px;height:114px">
  <svg width="48" height="48" viewBox="0 0 48 48" fill="none" stroke="#fff" stroke-width="2.5"><path d="M6 24 L24 8 L42 24"/><path d="M12 20 V40 H26"/><circle cx="32" cy="32" r="6"/><path d="M36 36 L42 42"/></svg>
</div>

<div class="abs benefit-name" style="left:70px;top:1638px">AENEAN A ENIM NIBH</div>
<div class="abs benefit-text" style="left:90px;top:1672px">Bauris consectetur libero, sit amet eleifend quam.</div>
<div class="abs benefit-name" style="left:792px;top:1638px">MENEAN A ENIM NIBH</div>
<div class="abs benefit-text" style="left:812px;top:1672px">Bauris consectetur libero, sit amet eleifend quam.</div>
<div class="abs benefit-name" style="left:430px;top:1835px">OENEAN A ENIM NIBH</div>
<div class="abs benefit-text" style="left:450px;top:1870px">Mauris consectetur libero, sit amet eleifend quam.</div>
<div class="abs benefit-name" style="left:70px;top:1897px">BENEAN A ENIM NIBH</div>
<div class="abs benefit-text" style="left:90px;top:1931px">Bauris consectetur libero, sit amet eleifend quam.</div>
<div class="abs benefit-name" style="left:792px;top:1897px">SENEAN A ENIM NIBH</div>
<div class="abs benefit-text" style="left:812px;top:1931px">Bauris consectetur libero, sit amet eleifend quam.</div>

<!-- Property Highlights -->
<h2 class="abs h-dark" style="left:98px;top:2134px;font-size:38px">Our</h2>
<h2 class="abs h-accent" style="left:98px;top:2184px;font-size:38px">Property Highlights</h2>
<p class="abs hl-p" style="top:2258px">Nemo enim ipsam voluptatem quia voluptas sit aspernatur aut odit aut fugit, sed quia consequuntur magni dolores eos qui ratione voluptatem sequi nesciunt.</p>
<div class="abs acc acc-open" style="top:2335px">
  <svg width="26" height="26" viewBox="0 0 26 26"><circle cx="13" cy="13" r="12" fill="#fff"/><path d="M8 13 L12 17 L19 9" fill="none" stroke="#8fa6c9" stroke-width="2.5"/></svg>Property Description</div>
<p class="abs hl-p" style="left:155px;width:560px;top:2398px">Nemo enim ipsam voluptatem quia voluptas sit aspernatur aut odit aut fugit, sed quia consequuntur magni dolores eos qui ratione voluptatem sequi nesciunt.</p>
<div class="abs acc acc-row" style="top:2472px">
  <svg width="26" height="26" viewBox="0 0 26 26"><path d="M7 13 L11 17 L19 9" fill="none" stroke="#1e1e1e" stroke-width="3"/></svg>Living Space</div>
<div class="abs acc acc-row" style="top:2531px">
  <svg width="26" height="26" viewBox="0 0 26 26"><path d="M7 13 L11 17 L19 9" fill="none" stroke="#1e1e1e" stroke-width="3"/></svg>Other Info</div>
<div class="abs hl-photo" role="img" aria-label="Shingled lakefront house with boat dock"></div>

<!-- Gallery -->
<div class="abs gallery"></div>
<h2 class="abs sec-title" style="top:2734px;color:var(--ink)"><span class="h-dark">Our</span> <span class="h-accent">Gallery</span></h2>
<div class="abs tile" style="left:100px;top:2853px;width:444px;height:460px;background:linear-gradient(180deg,#5e6672 0%,#6b7178 40%,#5b5249 65%,#3f4a3a 100%)" role="img" aria-label="Stone cottage with steep slate roof under overcast sky"></div>
<div class="abs caption">NEMO ENIM IPSAM VOLUPTATEM</div>
<div class="abs tile" style="left:568px;top:2853px;width:534px;height:217px;background:linear-gradient(180deg,#8fb0d8 0%,#a7c0da 35%,#9a8c74 60%,#5f7d3c 85%,#6c8d44 100%)" role="img" aria-label="Large stone estate home with green lawn"></div>
<div class="abs tile" style="left:568px;top:3096px;width:255px;height:217px;background:linear-gradient(180deg,#9fc0e2 0%,#b4c7d8 35%,#a68e72 60%,#6f8a4a 100%)" role="img" aria-label="Brick and stone suburban home"></div>
<div class="abs tile" style="left:846px;top:3096px;width:256px;height:217px;background:linear-gradient(180deg,#a9bfd4 0%,#9a8a78 45%,#7b6f62 70%,#b0a89a 100%)" role="img" aria-label="Stone manor with paved driveway"></div>
<svg class="abs" style="left:36px;top:3068px" width="20" height="30" viewBox="0 0 20 30" fill="none" stroke="#8fa6c9" stroke-width="2.5"><path d="M15 3 L4 15 L15 27"/></svg>
<svg class="abs" style="left:1138px;top:3068px" width="20" height="30" viewBox="0 0 20 30" fill="none" stroke="#8fa6c9" stroke-width="2.5"><path d="M5 3 L16 15 L5 27"/></svg>

<!-- Footer -->
<div class="abs footer"></div>
<div class="abs brand" style="left:98px;top:3478px;font-size:34px">HEARTH LANE</div>
<p class="abs foot-text">Nemo enim ipsam voluptatem quia voluptas sit aspernatur aut odit aut fugit, sed quia consequuntur magni dolores eos qui ratione voluptatem sequi nesciunt. Neque porro quisquam est, qui dolorem ipsum quia dolor sit amet.</p>
<div class="abs social" style="left:99px;top:3701px"></div>
<div class="abs social" style="left:143px;top:3701px"></div>
<div class="abs social" style="left:187px;top:3701px"></div>
<div class="abs social" style="left:231px;top:3701px"></div>

<div class="abs foot-h" style="left:624px;top:3476px">Quick Links</div>
<div class="abs foot-rule" style="left:624px;top:3514px"></div>
<ul class="abs links">
  <li><svg width="16" height="14" viewBox="0 0 16 14" fill="none" stroke="#fff" stroke-width="1.5"><path d="M1 7 H13 M8 2 L13 7 L8 12"/></svg>Home</li>
  <li><svg width="16" height="14" viewBox="0 0 16 14" fill="none" stroke="#fff" stroke-width="1.5"><path d="M1 7 H13 M8 2 L13 7 L8 12"/></svg>Qeno</li>
  <li><svg width="16" height="14" viewBox="0 0 16 14" fill="none" stroke="#fff" stroke-width="1.5"><path d="M1 7 H13 M8 2 L13 7 L8 12"/></svg>About Qe No Home</li>
  <li><svg width="16" height="14" viewBox="0 0 16 14" fill="none" stroke="#fff" stroke-width="1.5"><path d="M1 7 H13 M8 2 L13 7 L8 12"/></svg>Downloads</li>
  <li><svg width="16" height="14" viewBox="0 0 16 14" fill="none" stroke="#fff" stroke-width="1.5"><path d="M1 7 H13 M8 2 L13 7 L8 12"/></svg>Contact us</li>
</ul>

<div class="abs foot-h" style="left:872px;top:3476px">Contact Us</div>
<div class="abs foot-rule" style="left:872px;top:3514px"></div>
<div class="abs contact-icon" style="left:872px;top:3549px"><svg width="14" height="18" viewBox="0 0 14 18" fill="none" stroke="#fff" stroke-width="1.6"><path d="M7 17 C2 11 1 8 1 6.5 A6 6 0 0 1 13 6.5 C13 8 12 11 7 17Z"/><circle cx="7" cy="6.5" r="2"/></svg></div>
<div class="abs" style="left:926px;top:3548px"><div class="contact-lbl">ADDRESS,</div><div class="contact-val">48 Birchwood Drive,<br>Lakeview 2210</div></div>
<div class="abs contact-icon" style="left:872px;top:3631px"><svg width="16" height="16" viewBox="0 0 16 16" fill="none" stroke="#fff" stroke-width="1.6"><path d="M3 1 L6 1 L7 5 L5 6.5 C6 9 7 10 9.5 11 L11 9 L15 10 L15 13 C15 14 14 15 13 15 C6 15 1 10 1 3 C1 2 2 1 3 1Z"/></svg></div>
<div class="abs" style="left:926px;top:3632px"><div class="contact-lbl">PHONE:</div><div class="contact-val">Phone: +180 555 0142</div></div>
<div class="abs contact-icon" style="left:872px;top:3698px"><svg width="16" height="12" viewBox="0 0 16 12" fill="none" stroke="#fff" stroke-width="1.6"><rect x="1" y="1" width="14" height="10"/><path d="M1 1 L8 7 L15 1"/></svg></div>
<div class="abs" style="left:926px;top:3700px"><div class="contact-lbl">Mail:</div><div class="contact-val">info@hearthlanerealty.com</div></div>

<div class="abs foot-line"></div>
<div class="abs copy">Copyrights © 2018 Hearth Lane Realty Group. All Rights Reserved.</div>

</body>
</html>
```